business card deign

Logo needs the following on it.
1. attached logo
2. Tagline - "If it keeps a drink cold or the party going...we do it!"
3. Name- Dalton Pikes, Founder and CPO
4. Address - 412 E. Carver Avenue, Ste 2207, Tampa, FL. 33917
5. Phone - 555.318.4726

```html
<!DOCTYPE html>
<html lang="en">
<head>
<meta charset="UTF-8">
<title>Hopvale Business Card</title>
<link rel="stylesheet" href="https://fonts.googleapis.com/css2?family=Roboto+Condensed:wght@400;700&family=Arimo:wght@400&display=swap">
<style>
  :root {
    --backdrop: #d3d4d6;
    --card: #141414;
    --ink: #ffffff;
    --ink-soft: #e8e8e8;
  }
  * { margin: 0; padding: 0; box-sizing: border-box; }
  html, body {
    width: 900px;
    height: 1200px;
    overflow: hidden;
    background: var(--backdrop);
  }
  .sheet {
    position: relative;
    width: 900px;
    height: 1200px;
  }
  .card {
    position: absolute;
    left: 134px;
    width: 630px;
    height: 357px;
    background: var(--card);
    color: var(--ink);
  }
  .card--front { top: 214px; }
  .card--back { top: 628px; }

  .brand-mark {
    position: absolute;
    border-radius: 50%;
    background: var(--ink);
  }
  .wordmark {
    position: absolute;
    font-family: "Roboto Condensed", sans-serif;
    font-weight: 700;
    color: var(--ink);
    text-transform: uppercase;
    line-height: 1;
    white-space: nowrap;
    text-align: center;
  }

  .card--front .brand-mark {
    left: 265px;
    top: 100px;
    width: 100px;
    height: 100px;
  }
  .card--front .wordmark {
    left: 0;
    width: 630px;
    top: 242px;
    font-size: 42px;
    letter-spacing: 0.32em;
    padding-left: 0.32em;
  }
  .tagline {
    position: absolute;
    left: 0;
    width: 630px;
    top: 305px;
    text-align: center;
    font-family: "Roboto Condensed", sans-serif;
    font-weight: 700;
    font-size: 16px;
    letter-spacing: 0.06em;
    color: var(--ink);
  }

  .card--back .brand-mark {
    left: 156px;
    top: 118px;
    width: 70px;
    height: 70px;
  }
  .card--back .wordmark {
    left: 91px;
    width: 200px;
    top: 226px;
    font-size: 29px;
    letter-spacing: 0.3em;
    padding-left: 0.3em;
  }
  .divider {
    position: absolute;
    left: 315px;
    top: 97px;
    width: 2px;
    height: 164px;
    background: var(--ink);
  }
  .contact {
    position: absolute;
    left: 343px;
    top: 100px;
    font-family: "Arimo", sans-serif;
    color: var(--ink-soft);
  }
  .contact__name {
    font-family: "Roboto Condensed", sans-serif;
    font-weight: 700;
    font-size: 29px;
    color: var(--ink);
    text-transform: uppercase;
    line-height: 1;
    letter-spacing: 0.01em;
  }
  .contact__role {
    margin-top: 10px;
    font-size: 14px;
  }
  .contact__phone {
    margin-top: 22px;
    font-size: 17px;
    letter-spacing: 0.06em;
    display: flex;
    align-items: center;
    gap: 7px;
  }
  .contact__phone svg { width: 11px; height: 11px; fill: var(--ink); }
  .contact__address {
    margin-top: 14px;
    font-size: 14.5px;
    line-height: 25px;
    font-style: normal;
  }
</style>
</head>
<body>
  <main class="sheet">
    <section class="card card--front">
      <span class="brand-mark" aria-hidden="true"></span>
      <div class="wordmark">Hopvale</div>
      <p class="tagline">If it keeps a drink cold or the party going...we do it!</p>
    </section>

    <section class="card card--back">
      <span class="brand-mark" aria-hidden="true"></span>
      <div class="wordmark">Hopvale</div>
      <div class="divider"></div>
      <div class="contact">
        <h1 class="contact__name">Dalton Pikes</h1>
        <p class="contact__role">Founder and CPO</p>
        <p class="contact__phone">
          <svg viewBox="0 0 24 24" aria-hidden="true"><path d="M6.6 10.8a15.1 15.1 0 0 0 6.6 6.6l2.2-2.2a1 1 0 0 1 1-.25 11.4 11.4 0 0 0 3.6.57 1 1 0 0 1 1 1V20a1 1 0 0 1-1 1A17 17 0 0 1 3 4a1 1 0 0 1 1-1h3.5a1 1 0 0 1 1 1c0 1.25.2 2.45.57 3.57a1 1 0 0 1-.25 1z"/></svg>
          555.318.4726
        </p>
        <address class="contact__address">
          412 E. Carver Avenue, Ste 2207<br>
          Tampa, FL. 33917
        </address>
      </div>
    </section>
  </main>
</body>
</html>
```